Defense contractor needs a roll-up for an exhibition

The booth we have booked has only a size of 3m².
So this will be the centerpiece of the whole booth.
We need a roll-up that attracts visitors and at the same time it should contain already designed graphics. These graphics are giving visitors an overview of our system. So it is necessary to have them exposed in a height that the booth personal can conveniently point with its fingers at them.
For information about our company and product visit:
https://www.brellowtrackline.com/
For designing you should use Adobe Illustrator and the templates provided in the zip file, to guarantee a perfect print.
I have supplied my business card that you can copy the logo. As the company logo will be already at the booth nearby the top of the roll-up, you should not place it there. It can be in the middle or at the bottom.
I have uploaded a picture of the booth. The roll up will be placed at the left of the screen and has a size of 80cm x 200cm

Defense

Defense

Serif

0054AA
0677BA
7BADD7
CADEEF
E8F1F8

• you must use the Adobe Illustrator template to have a good printing result
• company logo on the upper side of the roll-up

```html
<!DOCTYPE html>
<html lang="en">
<head>
<meta charset="utf-8">
<title>Advanced Combat Training Systems – Roll-up</title>
<link rel="stylesheet" href="https://fonts.googleapis.com/css2?family=Anton&family=Poppins:wght@400;500;600;700;800&family=Roboto+Condensed:wght@400&display=swap">
<style>
  :root {
    --navy: #1b2a8c;
    --navy-deep: #0f1a63;
    --black: #0b0b0b;
    --white: #ffffff;
    --lavender: #e5e8f8;
    --render-grey: #c9ccd8;
    --render-light: #f4f5fb;
    --sky-pink: #d98aa0;
    --sky-orange: #e9a070;
    --sky-blue: #3c57b8;
  }
  html, body {
    margin: 0;
    padding: 0;
    width: 1200px;
    height: 4000px;
    overflow: hidden;
    background: var(--white);
  }
  .rollup {
    position: relative;
    width: 1200px;
    height: 4000px;
    overflow: hidden;
    font-family: "Poppins", sans-serif;
    color: var(--black);
  }
  .hero {
    position: absolute;
    left: 0; top: 0;
    width: 1200px; height: 1100px;
    background:
      radial-gradient(ellipse 520px 160px at 380px 780px, rgba(233,160,112,.75), transparent 70%),
      radial-gradient(ellipse 460px 140px at 820px 700px, rgba(217,138,160,.7), transparent 70%),
      radial-gradient(ellipse 700px 260px at 600px 820px, rgba(60,87,184,.8), transparent 75%),
      linear-gradient(180deg, var(--navy-deep) 0%, var(--navy) 45%, var(--sky-blue) 75%, #2a3f9e 100%);
  }
  .hero-title {
    position: absolute;
    left: 0; top: 50px;
    width: 1200px;
  }
  .ground-band {
    position: absolute;
    left: 0; top: 1030px;
    width: 1200px; height: 210px;
    background: var(--black);
  }
  .services-tab {
    position: absolute;
    left: 0; top: 1100px;
    width: 1200px; height: 140px;
  }
  .content-bg {
    position: absolute;
    left: 0; top: 1240px;
    width: 1200px; height: 1150px;
    background: var(--white);
  }
  .services-heading {
    position: absolute;
    left: 0; top: 1112px;
    width: 1200px;
    margin: 0;
    text-align: center;
    font-weight: 800;
    font-size: 118px;
    line-height: 120px;
    letter-spacing: 1px;
  }
  .services-box {
    position: absolute;
    left: 95px; top: 1300px;
    width: 998px; height: 1030px;
    border: 6px solid var(--black);
    border-radius: 44px;
  }
  .services-intro {
    position: absolute;
    left: 95px; top: 1330px;
    width: 1010px;
    margin: 0;
    text-align: center;
    font-size: 30px;
    line-height: 42px;
    font-weight: 400;
    white-space: nowrap;
  }
  .services-divider {
    position: absolute;
    left: 598px; top: 1560px;
    width: 4px; height: 730px;
    background: #555;
  }
  .service {
    position: absolute;
    width: 500px;
    text-align: center;
  }
  .service-icon {
    display: block;
    margin: 0 auto;
    width: 200px; height: 200px;
  }
  .service-label {
    margin: 18px 0 0;
    font-weight: 600;
    font-size: 38px;
    line-height: 48px;
  }
  .service--warranty { left: 100px; top: 1560px; }
  .service--spares { left: 600px; top: 1560px; }
  .service--maintenance { left: 100px; top: 1980px; }
  .service--logistics { left: 600px; top: 1980px; }
  .training-band {
    position: absolute;
    left: 0; top: 2390px;
    width: 1200px; height: 210px;
  }
  .training-heading {
    position: absolute;
    left: 0; top: 2418px;
    width: 1200px;
    margin: 0;
    text-align: center;
    font-weight: 600;
    font-size: 46px;
    line-height: 56px;
    text-transform: uppercase;
  }
  .system-overview {
    position: absolute;
    left: 0; top: 2600px;
    width: 1200px; height: 1230px;
    background:
      radial-gradient(ellipse 260px 170px at 300px 380px, var(--render-grey), transparent 75%),
      radial-gradient(ellipse 360px 240px at 760px 640px, var(--render-grey), transparent 75%),
      radial-gradient(ellipse 380px 90px at 780px 200px, rgba(201,204,216,.8), transparent 75%),
      radial-gradient(ellipse 600px 480px at 600px 520px, var(--render-light), var(--lavender) 80%);
  }
  .brand-name {
    position: absolute;
    left: 0; top: 3720px;
    width: 1200px;
    margin: 0;
    text-align: center;
    font-weight: 800;
    font-size: 72px;
    line-height: 90px;
    color: var(--black);
    letter-spacing: 2px;
  }
  .footer {
    position: absolute;
    left: 0; top: 3830px;
    width: 1200px; height: 170px;
  }
  .footer-url {
    position: absolute;
    left: 0; top: 3870px;
    width: 1200px;
    margin: 0;
    text-align: center;
    font-family: "Roboto Condensed", sans-serif;
    font-size: 64px;
    line-height: 80px;
    color: var(--white);
  }
  .footer-url a { color: inherit; text-decoration: none; }
</style>
</head>
<body>
<main class="rollup">

  <section class="hero" role="img" aria-label="Dusk sky with blue, pink and orange clouds behind the silhouette of a battle tank"></section>

  <svg class="hero-title" width="1200" height="460" viewBox="0 0 1200 460" aria-labelledby="title-text">
    <title id="title-text">Advanced Combat Training Systems for realistic combat simulation</title>
    <text x="600" y="140" text-anchor="middle" font-family="Anton, sans-serif" font-size="150" fill="#ffffff" textLength="1010" lengthAdjust="spacingAndGlyphs">ADVANCED COMBAT</text>
    <text x="600" y="290" text-anchor="middle" font-family="Anton, sans-serif" font-size="150" fill="#ffffff" textLength="1000" lengthAdjust="spacingAndGlyphs">TRAINING SYSTEMS</text>
    <text x="600" y="390" text-anchor="middle" font-family="Poppins, sans-serif" font-weight="700" font-size="58" fill="#ffffff" textLength="1010" lengthAdjust="spacingAndGlyphs">FOR REALISTIC COMBAT SIMULATION</text>
  </svg>

  <div class="ground-band"></div>
  <svg class="services-tab" width="1200" height="140" viewBox="0 0 1200 140" aria-hidden="true">
    <polygon points="300,0 900,0 935,140 265,140" fill="#ffffff"/>
  </svg>
  <div class="content-bg"></div>

  <h2 class="services-heading">SERVICES</h2>

  <div class="services-box"></div>
  <p class="services-intro">The signature of the contract is not the end - it is just the<br>beginning of a long-lasting partnership.We offer</p>
  <div class="services-divider"></div>

  <div class="service service--warranty">
    <svg class="service-icon" viewBox="0 0 200 200" aria-hidden="true">
      <circle cx="100" cy="100" r="94" fill="#1b2a8c" stroke="#0b0b0b" stroke-width="8"/>
      <path d="M100 40 l12 10 16-3 5 15 15 6-3 16 10 12-10 12 3 16-15 6-5 15-16-3-12 10-12-10-16 3-5-15-15-6 3-16-10-12 10-12-3-16 15-6 5-15 16 3z" fill="none" stroke="#fff" stroke-width="5" stroke-linejoin="round"/>
      <circle cx="100" cy="100" r="32" fill="none" stroke="#fff" stroke-width="5"/>
      <path d="M84 101 l11 11 22-24" fill="none" stroke="#fff" stroke-width="6" stroke-linecap="round" stroke-linejoin="round"/>
    </svg>
    <p class="service-label">Extended<br>Warranty Programs</p>
  </div>

  <div class="service service--spares">
    <svg class="service-icon" viewBox="0 0 200 200" aria-hidden="true">
      <circle cx="100" cy="100" r="94" fill="#1b2a8c" stroke="#0b0b0b" stroke-width="8"/>
      <path d="M140 70 A52 52 0 1 0 110 150" fill="none" stroke="#fff" stroke-width="6" stroke-linecap="round"/>
      <path d="M90 68 v34 l-16 14" fill="none" stroke="#fff" stroke-width="6" stroke-linecap="round" stroke-linejoin="round"/>
      <path d="M128 130 c0-14 22-14 26 0 c4 14 26 14 26 0 c0-14-22-14-26 0 c-4 14-26 14-26 0z" fill="none" stroke="#fff" stroke-width="6"/>
    </svg>
    <p class="service-label">Long-term Spare<br>Part Services</p>
  </div>

  <div class="service service--maintenance">
    <svg class="service-icon" viewBox="0 0 200 200" aria-hidden="true">
      <circle cx="100" cy="100" r="94" fill="#1b2a8c" stroke="#0b0b0b" stroke-width="8"/>
      <rect x="62" y="52" width="72" height="100" rx="6" fill="none" stroke="#fff" stroke-width="5"/>
      <rect x="82" y="44" width="32" height="16" rx="4" fill="#1b2a8c" stroke="#fff" stroke-width="5"/>
      <line x1="74" y1="78" x2="120" y2="78" stroke="#fff" stroke-width="5"/>
      <line x1="74" y1="94" x2="112" y2="94" stroke="#fff" stroke-width="5"/>
      <line x1="74" y1="136" x2="110" y2="136" stroke="#fff" stroke-width="5"/>
      <path d="M150 80 l10 10 -42 42 -14 4 4 -14z" fill="none" stroke="#fff" stroke-width="5" stroke-linejoin="round"/>
    </svg>
    <p class="service-label">Maintenance Contracts</p>
  </div>

  <div class="service service--logistics">
    <svg class="service-icon" viewBox="0 0 200 200" aria-hidden="true">
      <circle cx="100" cy="100" r="94" fill="#1b2a8c" stroke="#0b0b0b" stroke-width="8"/>
      <path d="M60 100 a40 40 0 0 1 80 0" fill="none" stroke="#fff" stroke-width="6"/>
      <rect x="52" y="94" width="16" height="30" rx="6" fill="#fff"/>
      <rect x="132" y="94" width="16" height="30" rx="6" fill="#fff"/>
      <path d="M140 124 q0 20 -28 22" fill="none" stroke="#fff" stroke-width="5"/>
      <path d="M58 158 q42 -26 84 0" fill="none" stroke="#fff" stroke-width="6" stroke-linecap="round"/>
    </svg>
    <p class="service-label">Logistics Support</p>
  </div>

  <svg class="training-band" width="1200" height="210" viewBox="0 0 1200 210" aria-hidden="true">
    <rect width="1200" height="210" fill="#1b2a8c"/>
    <polygon points="255,20 945,20 1000,140 200,140" fill="#ffffff"/>
    <rect x="0" y="140" width="1200" height="70" fill="#1b2a8c"/>
    <line x1="215" y1="20" x2="150" y2="140" stroke="#ffffff" stroke-width="8"/>
    <line x1="985" y1="20" x2="1050" y2="140" stroke="#ffffff" stroke-width="8"/>
  </svg>
  <h3 class="training-heading">Equip your fighting<br>force with precision training</h3>

  <section class="system-overview" role="img" aria-label="Isometric system overview graphic: two training tanks at left, three target stations at top and a mobile command truck with operators at monitors at right"></section>

  <p class="brand-name">BRELLOW TRACKLINE</p>

  <svg class="footer" width="1200" height="170" viewBox="0 0 1200 170" aria-hidden="true">
    <rect width="1200" height="170" fill="#0b0b0b"/>
    <polygon points="0,30 110,170 0,170" fill="#1b2a8c"/>
    <polygon points="1200,30 1090,170 1200,170" fill="#1b2a8c"/>
  </svg>
  <p class="footer-url"><a href="https://www.brellowtrackline.com/">www.brellowtrackline.com</a></p>

</main>
</body>
</html>
```